Web Design job: SaaS start-up needs a cutting-edge web design

What's Needed:
- All designs files created
- Fully coded implementation in HTML/CSS/Bootstrap
- Pages: 5 -- see content here http://www.TeamVerdexa.com
-- Home Page
-- The Hidden Value
-- Benefits
-- About us
-- Careers
- The existing site has the textual content for each page. We can tweak to meet specific designs if needed.
- You will need to update/create image and interactive content for pages.

Reference:
Our existing website has a lot of content on it for reference -
http://www.TeamVerdexa.com

Description:
We need a web design that focuses in the UX and conveys the idea of magically fixing company problems by way of using our software.

Home Page
The main goal is to Drive Sales of the SaaS tool. When a visitor lands on our home page they should see: What we do, How we can help their problem and How to contact us.
1. Quickly understand What We Do
-- we sell SaaS software.
-- Need to quickly convey what our software does. It's seems complicated but really its not. See the description in about us for more info and visit our existing site.

2. How we can help their problem
-- We aim to solve any problem related to employees
-- Even if the visitor does not have a specific problem in mind, there are several areas organizations can always improve: (some examples below)
---- Create Stronger, More Productive Teams
---- Build Better Communications Pathways
---- Encourage Innovation and Positive Change
---- Develop and Retain Strong "Company Culture"

3. Be able to Contact Us to get started
-- contacting us to get a sales lead is the ultimate goal.
-- the user should not have to hunt to contact us. needs to be easy.

Other Pages (Hidden Value, Benefit, About Us, Careers):
-- These are informative pages about our software and process.
-- If we grab the attention of the user on the home page then these are the pages that they will explore for more info.
-- Should be able to link to these pages from the main nav or from sections with the homepage. For example: What We Do sections could link to the benefits page. How we help their problem sections could link to the Hidden Value page. Regardless of what links to where, the idea is that we will be able to nav to other areas.

About Us:
Our company name is TeamVerdexa (as in Organizational Analysis). We provide a software as a service (SaaS) that uses a simple 6-question survey to analyze the relationships of people within an Organization and provide leaders with ground-breaking Insights about their teams, interactive social network data visualizations to explore their team's composition and we give detailed profiles of the key players (i.e, who are the Social Bridges, Who are the Knowledge Bottlenecks, Who are the Best Mentors, Who are the people that are completely disconnected/out of the loop). Leaders then use this information to make high level organizational decisions.

What's unique about our software:
-- Powerful analysis results from just a 6-question "pulse-surveys"
-- Innovative Tools for visually exploring the organization through relationships as opposed to org-chart
-- Get real-time results as opposed to waiting months with traditional methods
-- Traditional Org-charts represent the organization's skeleton, whereas we uncover the organization's neural network (how it solves problems).

Preferred fonts (but could be convinced otherwise if looks great):
-- Section titles - Aleo
-- Main body - Lato
-- TeamVerdexa logo - Philosopher

Things we like:
-- We like a big slider as the top of the landing page.

Colors to include:
-- Colors in the logo (red, blue, green, teal) as accent colors

Feel of the site:
-- Cutting-edge Software
-- Professional
-- Social Network flare (we analyze relationships)

Note:
If we find a great match with a designer there is strong possibility to continue the relationship with follow on work redesigning our web-based application.

Target Market(s)

Current customers are Morrow Pike & Fenwell, Clearbrook Valley Bank.
We target anyone that manages a large team. Such as Corporate Leaders, High Level Managers, HR Leaders

Industry/Entity Type

Business Software

Contact Information for Business Card

Logo image
Name of company "TEAMVERDEXA" In Philosopher font.
Tagline: "Unlock the Hidden Value In Your Teams"
Person's Name, Title, email, phone.

Coding

Coded - Design and coding required

Number of Pages Required

4 page

Font styles to use
Other font styles liked:
• Lato, Philosopher, Aero

Colors
ec1f27
0255a3

Requirements
Must have
• See description.
Nice to have
• Things we like:
• We like a big slider as the top of the landing page. Ours is a little clunky and outdated but something fresh and sleek would be great.
• Colors to include:
• We would like to use the colors in the logo as accent colors in the site to give a consistent look and feel.
• Feel of the site:
• Cutting-edge Software
• Professional
• Social Network flare (we analyze relationships)

```html
<!DOCTYPE html>
<html lang="en">
<head>
<meta charset="utf-8">
<title>TeamVerdexa – Fast and Easy Assessments</title>
<link href="https://fonts.googleapis.com/css2?family=Aleo:wght@400;700&family=Lato:wght@400;700&family=Philosopher:wght@400;700&display=swap" rel="stylesheet">
<style>
  :root{
    --red:#ec1f27;
    --blue:#0255a3;
    --navy:#2b3990;
    --ink:#222;
    --grey-band:#d4d4d4;
    --footer:#e8e8e8;
    --footer-bar:#dcdcdc;
    --white:#fff;
  }
  *{box-sizing:border-box;margin:0;padding:0}
  html,body{width:1200px;height:2239px;overflow:hidden;background:var(--white)}
  body{position:relative;font-family:'Lato',sans-serif;color:var(--ink)}
  .abs{position:absolute}

  /* Header */
  .site-header{position:absolute;left:0;top:0;width:1200px;height:100px;border-bottom:1px solid #e2e2e2;background:var(--white)}
  .brand{position:absolute;left:161px;top:34px;display:flex;align-items:center;gap:12px}
  .brand-dot{width:30px;height:30px;border-radius:50%;background:var(--red)}
  .brand-name{font-family:'Philosopher',sans-serif;font-weight:700;font-size:25px;color:var(--navy);letter-spacing:.5px}
  .main-nav{position:absolute;left:552px;top:52px;display:flex;gap:17px;font-size:12px;text-transform:uppercase}
  .main-nav a{color:var(--blue);text-decoration:none}
  .main-nav a.active{color:var(--red)}
  .nav-caret{position:absolute;left:557px;top:93px;width:0;height:0;border-left:7px solid transparent;border-right:7px solid transparent;border-bottom:7px solid #d8d8d8}

  /* Hero */
  .hero{position:absolute;left:0;top:101px;width:1200px;height:454px;background:var(--white)}
  .hero-title{position:absolute;left:182px;top:204px;font-family:'Aleo',serif;font-weight:700;font-size:22px;color:var(--blue)}
  .hero-list{position:absolute;left:182px;top:256px;list-style:none}
  .hero-list li{position:relative;height:39.6px;padding-left:25px;font-size:10.5px;color:var(--red);line-height:16px}
  .hero-list li::before{content:"";position:absolute;left:0;top:1px;width:14px;height:14px;border-radius:50%;background:#e6e6e6}
  .hero-list li::after{content:"";position:absolute;left:4px;top:5px;width:4px;height:4px;border-right:1.5px solid var(--red);border-top:1.5px solid var(--red);transform:rotate(45deg)}
  .btn{display:inline-flex;align-items:center;justify-content:center;text-decoration:none}
  .btn-demo{position:absolute;left:179px;top:452px;width:221px;height:41px;background:var(--red);color:var(--white);font-family:'Aleo',serif;font-size:15px;border-radius:2px}
  .hero-art{position:absolute;left:575px;top:134px;width:455px;height:351px;background:radial-gradient(ellipse at center,#f3f5fa 0%,#fff 75%)}
  .slider-dots{position:absolute;left:570px;top:512px;display:flex;gap:5px}
  .slider-dots span{width:12px;height:12px;border-radius:50%;border:1.5px solid #999}
  .slider-dots span.on{background:var(--red);border-color:var(--red)}

  /* What we do */
  .what-we-do{position:absolute;left:0;top:555px;width:1200px;height:479px;background:var(--blue);color:var(--white)}
  .section-title{font-family:'Aleo',serif;font-weight:700;font-size:30px;text-align:center;letter-spacing:.5px}
  .what-we-do .section-title{position:absolute;left:0;top:57px;width:100%;color:var(--white)}
  .service{position:absolute;top:195px;width:240px;text-align:center;font-family:'Aleo',serif;font-size:21px;line-height:40px}
  .service svg{display:block;margin:0 auto 30px}

  /* How we help */
  .how-we-help{position:absolute;left:0;top:1034px;width:1200px;height:603px;background:linear-gradient(180deg,#fff 0%,#f6f6f6 50%,#fff 100%)}
  .how-we-help .section-title{position:absolute;left:0;top:72px;width:100%;color:#1a1a1a}
  .section-sub{position:absolute;left:0;top:117px;width:100%;text-align:center;font-size:11px;text-transform:uppercase;color:#333}
  .section-sub::before,.section-sub::after{content:"";position:absolute;top:7px;width:65px;border-top:1px solid #333}
  .section-sub::before{left:482px}
  .section-sub::after{left:651px}
  .help-card{position:absolute;left:206px;width:824px;height:160px;background:var(--white);box-shadow:0 8px 14px rgba(0,0,0,.12)}
  .help-card svg{position:absolute;left:0;top:0}
  .card-num{position:absolute;font-family:'Aleo',serif;font-size:26px;color:var(--white)}
  .card-heading{position:absolute;font-family:'Aleo',serif;font-weight:700;font-size:17px;line-height:21px;text-transform:uppercase;color:#111}
  .card-text{position:absolute;left:428px;top:48px;width:290px;font-size:10px;line-height:15px;color:#222}
  .card-list{position:absolute;left:78px;top:40px;list-style:none;font-size:10px}
  .card-list li{position:relative;padding-left:22px;height:21.3px}
  .card-list li::before{content:"";position:absolute;left:0;top:3px;width:5px;height:5px;border:1px solid #333;border-radius:50%}

  /* CTA */
  .cta{position:absolute;left:0;top:1637px;width:1200px;height:239px;background:var(--red)}
  .cta-text{position:absolute;left:179px;top:72px;font-family:'Aleo',serif;font-weight:700;font-size:27px;line-height:41px;color:var(--white);text-transform:uppercase}
  .btn-contact{position:absolute;left:775px;top:94px;width:197px;height:48px;background:var(--blue);color:var(--white);font-family:'Aleo',serif;font-weight:700;font-size:19px}

  /* Footer */
  .site-footer{position:absolute;left:0;top:1876px;width:1200px;height:325px;background:var(--footer)}
  .footer-brand{position:absolute;left:228px;top:28px;width:300px}
  .footer-brand .brand-dot{width:44px;height:44px;margin-left:74px;margin-bottom:18px}
  .footer-brand .brand-name{font-size:24px;display:block}
  .footer-about{position:absolute;left:227px;top:158px;width:275px;font-size:10px;line-height:16px;text-align:justify;color:#222}
  .footer-heading{position:absolute;font-family:'Aleo',serif;font-size:18px;color:#222}
  .footer-links{position:absolute;left:600px;top:139px;list-style:none;font-size:10.5px}
  .footer-links li{height:25.7px}
  .footer-links a{color:#222;text-decoration:none}
  .email-field{position:absolute;left:781px;top:133px;width:194px;height:30px;background:var(--white);border:none;font-family:'Lato',sans-serif;font-size:9px;padding-left:12px;color:#444}
  .btn-subscribe{position:absolute;left:784px;top:173px;width:92px;height:30px;background:var(--red);color:var(--white);font-size:12px}
  .social{position:absolute;left:781px;top:262px;display:flex;gap:15px}
  .social span{width:14px;height:14px;border-radius:50%;background:#666}
  .footer-bar{position:absolute;left:0;top:2201px;width:1200px;height:38px;background:var(--footer-bar);text-align:center;font-size:10px;line-height:38px;color:#333}
</style>
</head>
<body>

<header class="site-header">
  <a class="brand" href="#"><span class="brand-dot"></span><span class="brand-name">TEAMVERDEXA</span></a>
  <nav class="main-nav">
    <a class="active" href="#">Home</a>
    <a href="#">The Hidden Value</a>
    <a href="#">Benefits</a>
    <a href="#">About Us</a>
    <a href="#">Careers</a>
    <a href="#">Client Login</a>
  </nav>
  <span class="nav-caret"></span>
</header>

<section class="hero">
</section>
<h1 class="hero-title">FAST AND EASY ASSESSMENTS</h1>
<ul class="hero-list">
  <li>Simple Data Collection (6 Questions)</li>
  <li>Proven World-Class Algorithms</li>
  <li>Real-time Visual Exploration Capabilities</li>
  <li>Immediate Analyses and 24/7 Cloud-based Access</li>
  <li>Full Support and Guidance from our Experts</li>
</ul>
<a class="btn btn-demo" href="#">Get Started To FREE Demo</a>
<div class="hero-art" role="img" aria-label="Line illustration of a computer saying Hello with floppy disks, gears and the word SAAS"></div>
<div class="slider-dots"><span></span><span class="on"></span><span></span><span></span></div>

<section class="what-we-do">
  <h2 class="section-title">WHAT WE DO</h2>
  <div class="service" style="left:113px">
    <svg width="66" height="66" viewBox="0 0 66 66" fill="none" stroke="#fff" stroke-width="2.5"><rect x="3" y="6" width="60" height="40" rx="2"/><rect x="12" y="14" width="42" height="24"/><path d="M33 46v10M20 60h26"/><path d="M17 20h6M17 26h6M17 32h6M27 20h20M27 26h20M27 32h14"/></svg>
    ONLINE PULSE<br>SURVEY
  </div>
  <div class="service" style="left:331px">
    <svg width="66" height="66" viewBox="0 0 66 66" fill="none" stroke="#fff" stroke-width="2.5"><circle cx="33" cy="10" r="6"/><circle cx="33" cy="34" r="6"/><circle cx="14" cy="54" r="6"/><circle cx="33" cy="56" r="6"/><circle cx="52" cy="54" r="6"/><path d="M33 16v12M29 39l-11 10M33 40v10M37 39l11 10"/></svg>
    PROPRIETARY<br>ALGORITHMS
  </div>
  <div class="service" style="left:567px">
    <svg width="80" height="66" viewBox="0 0 80 66" fill="none" stroke="#fff" stroke-width="2.5"><circle cx="22" cy="36" r="13" stroke-dasharray="5 3"/><circle cx="22" cy="36" r="5"/><circle cx="52" cy="16" r="10" stroke-dasharray="4 3"/><circle cx="52" cy="16" r="4"/><circle cx="58" cy="46" r="11" stroke-dasharray="4 3"/><circle cx="58" cy="46" r="4"/></svg>
    ORGANIZATIONAL<br>KEY INSIGHTS
  </div>
  <div class="service" style="left:823px">
    <svg width="66" height="66" viewBox="0 0 66 66" fill="none" stroke="#fff" stroke-width="2.5"><path d="M6 30a27 27 0 0 0 54 0"/><path d="M10 22h14l9 8 9-8h14"/><path d="M20 30l10 10M26 28l10 10M32 28l8 8"/></svg>
    EXPERT REVIEW &amp;<br>ACTION PLAN
  </div>
</section>

<section class="how-we-help">
  <h2 class="section-title">HOW WE HELP ?</h2>
  <p class="section-sub">Their Problem</p>

  <article class="help-card" style="top:163px">
    <svg width="824" height="160" viewBox="0 0 824 160">
      <polygon points="0,0 418,0 333,160 93,160" fill="var(--grey-band)"/>
      <polygon points="0,0 134,0 55,84" fill="var(--blue)"/>
    </svg>
    <span class="card-num" style="left:39px;top:18px">01</span>
    <h3 class="card-heading" style="left:152px;top:36px">We aim to solve<br>any problem<br>related to<br>employees</h3>
    <p class="card-text">Duis aute irure dolor in reprehenderit in voluptate velit esse cillum dolore eu fugiat nulla pariatur. Excepteur sint occaecat cupidatat non proident, sunt in culpa qui officia deserunt mollit anim id est laborum.</p>
  </article>

  <article class="help-card" style="top:353px">
    <svg width="824" height="160" viewBox="0 0 824 160">
      <polygon points="358,0 772,0 690,160 451,160" fill="var(--grey-band)"/>
      <polygon points="637,0 772,0 717,86" fill="var(--red)"/>
    </svg>
    <span class="card-num" style="left:686px;top:18px">02</span>
    <h3 class="card-heading" style="left:463px;top:36px">Even if the visitor<br>does not have a<br>specific problem in<br>mind, ...</h3>
    <ul class="card-list">
      <li>Create Stronger, More Productive Teams</li>
      <li>Build Better Communications Pathways</li>
      <li>Encourage Innovation and Positive Change</li>
      <li>Develop and Retain Strong "Company Culture"</li>
    </ul>
  </article>
</section>

<section class="cta">
  <p class="cta-text">Contacting us to get a sales lead<br>is the ultimate goal.</p>
  <a class="btn btn-contact" href="#">CONTACT US</a>
</section>

<footer class="site-footer">
  <div class="footer-brand"><span class="brand-dot" style="display:block"></span><span class="brand-name">TEAMVERDEXA</span></div>
  <p class="footer-about">Our company name is TeamVerdexa (as in Organizational Analysis). We provide a software as a service (SaaS) that uses a simple 6-question survey to analyze the relationships of people within an Organization and provide leaders with ground-breaking Insights about their teams, interactive social network data visualizations to explore their team's composition and we give detailed profiles ....</p>

  <h4 class="footer-heading" style="left:600px;top:97px">Navigation</h4>
  <ul class="footer-links">
    <li><a href="#">Home</a></li>
    <li><a href="#">The Hidden Value</a></li>
    <li><a href="#">Benefits</a></li>
    <li><a href="#">About Us</a></li>
    <li><a href="#">Careers</a></li>
    <li><a href="#">Client Login</a></li>
  </ul>

  <h4 class="footer-heading" style="left:779px;top:96px">Subscribe Newsletter</h4>
  <input class="email-field" type="email" placeholder="Enter Email id">
  <a class="btn btn-subscribe" href="#">Subscribe</a>
  <h4 class="footer-heading" style="left:779px;top:224px">Follow Us</h4>
  <div class="social"><span></span><span></span><span></span><span></span></div>
</footer>
<div class="footer-bar">© 2016 www.companyname.com</div>

</body>
</html>
```